Business Card Design

New business card design

Target Market(s)

Residential & Commercial Property Managers

Industry/Entity Type

Plumbing Services

Contact Information for Business Card

Name - Rowan Keddle, title - Director, Phone Number - 0431 286 517, email - rowan@tbk-plumbing.com.au, Company ABN - 73 215 904 386,

Font styles to use
Sans Serif

Colors
0054AA
0677BA
7BADD7
CADEEF
E8F1F8

```html
<!DOCTYPE html>
<html lang="en">
<head>
<meta charset="utf-8">
<title>TBK Plumbing Services – Business Card</title>
<link rel="stylesheet" href="https://fonts.googleapis.com/css2?family=Montserrat:wght@300;400;500;700&display=swap">
<style>
  :root {
    --stage: #2a2a2b;
    --card: #1b1b1c;
    --accent: #0aaef0;
    --muted: #8a7d70;
    --rule: #5a544e;
  }
  * { box-sizing: border-box; margin: 0; padding: 0; }
  html, body {
    width: 1200px; height: 1200px; overflow: hidden;
    background: var(--stage);
    font-family: "Montserrat", sans-serif;
  }
  .card {
    position: absolute;
    left: 286px;
    width: 628px;
    height: 376px;
    background: var(--card);
    box-shadow: 0 18px 40px rgba(0,0,0,0.45);
    overflow: hidden;
  }
  .card--front { top: 194px; }
  .card--back { top: 621px; }

  .brand {
    display: flex;
    align-items: center;
    gap: 14px;
    color: var(--muted);
    font-weight: 300;
    text-transform: lowercase;
  }
  .brand__dot {
    border-radius: 50%;
    background: var(--accent);
    flex: none;
  }
  .card--front .brand {
    position: absolute;
    left: 0; right: 0; top: 0; bottom: 0;
    justify-content: center;
    font-size: 30px;
    letter-spacing: 0.3em;
  }
  .card--front .brand__dot { width: 22px; height: 22px; }
  .card--back .brand {
    position: absolute;
    left: 30px; top: 70px;
    font-size: 17px;
    letter-spacing: 0.28em;
    gap: 10px;
  }
  .card--back .brand__dot { width: 14px; height: 14px; }

  .person {
    position: absolute;
    left: 30px; top: 250px;
  }
  .person__name {
    color: var(--accent);
    font-weight: 500;
    font-size: 19px;
    line-height: 1;
    text-transform: uppercase;
  }
  .person__name strong { font-weight: 700; }
  .person__title {
    color: var(--muted);
    font-size: 15px;
    margin-top: 4px;
  }
  .rule {
    position: absolute;
    left: 30px; right: 44px; top: 302px;
    height: 1px;
    background: var(--rule);
  }
  .contact {
    position: absolute;
    left: 30px; top: 313px;
    list-style: none;
    color: var(--muted);
    font-size: 14px;
    font-weight: 500;
  }
  .contact li {
    display: flex; align-items: center; gap: 7px;
    height: 21px;
  }
  .contact svg { width: 12px; height: 12px; fill: var(--accent); flex: none; }
  .abn {
    position: absolute;
    right: 44px; top: 313px;
    height: 21px; line-height: 21px;
    color: var(--muted);
    font-size: 14px;
    font-weight: 500;
  }
  .accent-bar {
    position: absolute;
    left: 0; right: 0; bottom: 0;
    height: 13px;
    background: var(--accent);
  }
</style>
</head>
<body>
  <section class="card card--front" aria-label="Card front">
    <div class="brand">
      <span class="brand__dot"></span>
      <span class="brand__name">tbk plumbing services</span>
    </div>
  </section>

  <section class="card card--back" aria-label="Card back">
    <div class="brand">
      <span class="brand__dot"></span>
      <span class="brand__name">tbk plumbing services</span>
    </div>

    <div class="person">
      <p class="person__name">Rowan <strong>Keddle</strong></p>
      <p class="person__title">Director</p>
    </div>

    <div class="rule"></div>

    <ul class="contact">
      <li>
        <svg viewBox="0 0 24 24" aria-hidden="true"><path d="M6.6 10.8a15.1 15.1 0 0 0 6.6 6.6l2.2-2.2c.3-.3.7-.4 1-.2 1.1.4 2.3.6 3.6.6.6 0 1 .4 1 1V20c0 .6-.4 1-1 1C10.6 21 3 13.4 3 4c0-.6.4-1 1-1h3.5c.6 0 1 .4 1 1 0 1.3.2 2.5.6 3.6.1.3 0 .7-.2 1l-2.3 2.2z"/></svg>
        <span>0431 286 517</span>
      </li>
      <li>
        <svg viewBox="0 0 24 24" aria-hidden="true"><path d="M2 5h20v14H2V5zm2 2v.5l8 5 8-5V7H4zm0 2.8V17h16V9.8l-8 5-8-5z"/></svg>
        <span>rowan@tbk-plumbing.com.au</span>
      </li>
    </ul>

    <p class="abn">ABN: 73 215 904 386</p>

    <div class="accent-bar"></div>
  </section>
</body>
</html>
```